WEDDING ENTERTAINMENT COMPANY NEEDS ONE PAGE PSD web design + business card design

Dear Designers,
'T.O.R.U Entertainment' is a professional Sydney-based company that provides Master of Ceremonies and DJ services at wedding receptions.
We're after an adaptive single page web design (with scroll up & down pages), and a business card design.
The site should be fully compatible with mobile devices. I need the design layouts for computer, tablets and mobile phone.
"Our mission is to rid the earth of boring weddings!", so our website should reflect this philosophy.
The final design should communicate that we're FUN and easy-going MC and DJ duet.
IMPORTANT:
1. We would like to see creative and fun-looking designs - not the average looking templates (like the ones Kettle Forge or other sites offer).
2. We want our site to have a vertical rhythm, fun and creative layout with clip-art illustrations, and cute little details like little drawings e.g. hearts, flowers, birds, bride and groom, etc...
Example of a website: http://sun-over-the-bay.fenrudo.net/#en
https://the-garden-party.lopreni.com/home-layouts/home-2/
A website similar in style to this illustration (also attached): http://thumb4.pictovelle.com/display_pic_with_logo/5817302/382904157/stock-vector-wedding-invitation-design-template-cartoon-pigeons-bride-groom-on-retro-bicycle-floral-frame-and-382904157.jpg
We'd like to see designs that use the color PINK, combined with the other most popular wedding colors for example: gold, turquoise or light blue. We'll leave it up to you.
The site should also work with the attached logo.
NOTE: We attached the doc with the page content:
-Buttons/links
-Sections
-Text for each section
-Notes for the designers (in YELLOW).
If you have any questions, please don't be shy to ask. ;)
Happy creating, and we're looking forward to seeing your designs!
Thanks,
R & L
Target Market(s)
Couples getting married
Industry/Entity Type
Wedding
Contact Information for Business Card
The business card design should be based on the website design - colors, style etc.
FRONT SIDE:
1). Logo 2). Our contact details (to be provided)
BACK SIDE:
1). Logo 2). Our mission: 'Let's rid the earth of boring weddings!' 3). Services: 'Wedding MC | Wedding DJ | Extensive Party Pre-Planning | State of the Art Music & Sound Equipment'
Number of Pages Required
1 page
Requirements
Must have
- IMPORTANT: Please send high res and full screen designs - so that we can see how the site will look like full screen.
- The site should work with the attached logo.
- Color PINK, combined with the other most popular wedding colors for example: gold, turquoise or light blue.
- IMPORTANT:
- 1. We would like to see creative and fun-looking designs - not the average looking templates (like the ones Kettle Forge or other sites offer).
- 2. We want our site to have a vertical rhythm, fun and creative layout with clip-art illustrations, and cute little details like little drawings e.g. hearts, flowers, birds, bride and groom, etc...
- Example of the website: http://sun-over-the-bay.fenrudo.net/#en
- https://the-garden-party.lopreni.com/home-layouts/home-2/
- A website similar in style to this illustration (attached):
- http://thumb4.pictovelle.com/display_pic_with_logo/5817302/382904157/stock-vector-wedding-invitation-design-template-cartoon-pigeons-bride-groom-on-retro-bicycle-floral-frame-and-382904157.jpg
Should not have
- No stock images/photos, only unique graphics, drawings, clip art illustrations

```html
<!DOCTYPE html>
<html lang="en">
<head>
<meta charset="utf-8">
<title>T.O.R.U Entertainment — Wedding MC &amp; DJ</title>
<link href="https://fonts.googleapis.com/css2?family=Playfair+Display:wght@400;700&family=Raleway:wght@400;500;600;700&family=Great+Vibes&display=swap" rel="stylesheet">
<style>
:root{
  --pink:#e0468a;
  --pink-light:#f36aa6;
  --pink-dark:#c93178;
  --pink-tint:#f9d3e3;
  --teal:#3dbcae;
  --teal-dark:#2fa699;
  --teal-tint:#d2f1ed;
  --orange:#f8a51d;
  --orange-light:#fbb93f;
  --orange-tint:#feebc6;
  --grey-bg:#efefef;
  --ink:#444;
  --ink-soft:#888;
  --dark:#2b2b2b;
  --white:#fff;
  --blue:#2e9fd8;
}
*{margin:0;padding:0;box-sizing:border-box}
html,body{width:1200px;height:4612px;overflow:hidden}
body{font-family:'Raleway',sans-serif;color:var(--ink);background:var(--white);font-size:13px;line-height:1.6}
.section-title{text-align:center;font-size:20px;font-weight:700;letter-spacing:2px;text-transform:uppercase;color:#555;line-height:1.3}
.divider{display:block;margin:6px auto 0}
/* header */
.site-header{height:150px;display:flex;align-items:center;justify-content:center;gap:12px}
.brand-mark{width:40px;height:40px;border-radius:50%;background:var(--pink)}
.brand-name{font-family:'Playfair Display',serif;font-size:22px;color:var(--pink);letter-spacing:2px}
.main-nav{height:55px;background:linear-gradient(90deg,var(--pink-dark),var(--pink-light));display:flex;justify-content:center;align-items:stretch}
.main-nav a{color:var(--white);text-decoration:none;font-size:12px;font-weight:600;letter-spacing:1px;padding:0 20px;display:flex;align-items:center}
.main-nav a.active{background:var(--teal)}
/* hero */
.hero{height:555px;position:relative;overflow:hidden}
.hero-photo{position:absolute;inset:0;background:linear-gradient(90deg,#fff 0%,#f7f1ee 30%,#e6d8d0 55%,#c9a79a 75%,#4a3a36 100%)}
.hero-copy{position:relative;width:440px;margin-left:110px;padding-top:90px}
.hero-copy h1{font-family:'Playfair Display',serif;font-size:64px;color:var(--pink);letter-spacing:3px;line-height:1}
.hero-copy .tagline{font-size:15px;font-weight:700;color:var(--pink);margin:14px 0 16px;text-transform:uppercase;letter-spacing:.5px;line-height:1.4}
.hero-copy p{color:#666;font-size:13px}
.btn{display:inline-block;background:var(--pink);color:var(--white);font-size:11px;font-weight:700;letter-spacing:1px;padding:12px 26px;border-radius:3px;margin-top:24px}
/* services */
.services{height:440px;padding-top:40px}
.service-cards{display:flex;justify-content:center;gap:30px;margin-top:36px}
.service-card{width:320px;height:300px;color:var(--white);text-align:center;padding:30px 28px;box-shadow:0 4px 10px rgba(0,0,0,.15)}
.service-card.pink{background:linear-gradient(160deg,var(--pink-light),var(--pink-dark))}
.service-card.teal{background:linear-gradient(160deg,#54cfc2,var(--teal-dark))}
.service-card.orange{background:linear-gradient(160deg,var(--orange-light),#f39313)}
.service-icon{width:84px;height:84px;border-radius:50%;margin:0 auto 20px;border:3px solid rgba(255,255,255,.9)}
.pink .service-icon{background:radial-gradient(circle,var(--white) 30%,var(--pink-tint))}
.teal .service-icon{background:radial-gradient(circle,var(--white) 30%,var(--teal-tint))}
.orange .service-icon{background:radial-gradient(circle,var(--white) 30%,var(--orange-tint))}
.service-card h3{font-size:12px;font-weight:700;letter-spacing:1px;margin-bottom:10px;line-height:1.4}
.service-card p{font-size:12px;line-height:1.55}
.service-card .more{display:block;margin-top:16px;font-size:11px;font-weight:700;letter-spacing:1px}
/* about */
.about{height:480px;background:var(--grey-bg);padding-top:40px}
.about-row{display:flex;justify-content:center;align-items:flex-start;gap:60px;margin-top:30px}
.member{width:280px;text-align:center}
.member-photo{width:180px;height:180px;border-radius:50%;border:6px solid var(--white);margin:0 auto;background:radial-gradient(circle at 50% 40%,#d9b5a2,#8a5b4d);box-shadow:0 2px 6px rgba(0,0,0,.15)}
.member-photo.him{background:radial-gradient(circle at 50% 40%,#cfd3d8,#56606c)}
.member-name{font-family:'Great Vibes',cursive;font-size:34px;color:var(--pink);margin-top:6px;line-height:1.3}
.member p{font-size:12px;color:#666;margin-top:6px}
.countdown{width:300px;text-align:center;padding-top:40px}
.countdown .day{font-size:22px;font-weight:600;color:#555;letter-spacing:2px}
.countdown .date{font-family:'Playfair Display',serif;font-size:30px;color:#444;line-height:1.3}
.count-boxes{display:flex;justify-content:center;gap:12px;margin-top:20px}
.count-box{width:56px;height:56px;border-radius:50%;background:var(--white);border:2px solid var(--pink);display:flex;flex-direction:column;align-items:center;justify-content:center}
.count-box b{font-size:17px;color:#444;line-height:1}
.count-box span{font-size:8px;color:var(--ink-soft);letter-spacing:1px;line-height:1.4}
/* why hire */
.why{height:600px;background:var(--teal);padding-top:40px;color:var(--white)}
.why .section-title{color:var(--white)}
.reasons{display:grid;grid-template-columns:repeat(3,300px);column-gap:80px;row-gap:60px;justify-content:center;margin-top:50px}
.reason{display:flex;gap:16px}
.reason-icon{flex:0 0 46px;height:46px;border:2px solid var(--white);border-radius:50%;display:flex;align-items:center;justify-content:center}
.reason h4{font-size:12px;font-weight:700;letter-spacing:1px;margin-bottom:4px}
.reason p{font-size:12px;opacity:.9}
/* couples */
.couples{height:540px;position:relative;color:var(--white);text-align:center;padding-top:40px}
.couples-photo{position:absolute;inset:0;background:linear-gradient(90deg,#3b3532,#5b514b 40%,#4a423e 70%,#2a2624)}
.couples-inner{position:relative}
.couples .section-title{color:var(--white)}
.couples blockquote{width:820px;margin:60px auto 0;font-size:14px;font-style:italic;line-height:1.8}
.couple-avatar{width:90px;height:90px;border-radius:50%;border:4px solid var(--white);margin:40px auto 12px;background:radial-gradient(circle,#c9a08f,#6d4d42)}
.couple-sign{font-size:13px;font-weight:700;letter-spacing:1px}
/* gallery */
.gallery{height:500px;padding-top:40px}
.gallery-grid{display:grid;grid-template-columns:260px 200px 260px 310px;grid-template-rows:200px 200px;width:1030px;margin:30px auto 0}
.gallery-intro{background:var(--pink);color:var(--white);text-align:center;padding:36px 30px}
.gallery-intro h3{font-family:'Playfair Display',serif;font-size:26px;letter-spacing:2px;line-height:1.3}
.gallery-intro p{font-size:12px;margin-top:10px}
.g1{grid-row:1/3;grid-column:2;background:linear-gradient(180deg,#c6cdbf,#7b8a6c)}
.g2{background:linear-gradient(160deg,#f2ece4,#c9b9a6)}
.g3{background:linear-gradient(160deg,#dfe6d8,#9fb08d)}
.g4{background:linear-gradient(160deg,#ead9d0,#b08b7b)}
.g5{background:linear-gradient(160deg,#e7e3de,#a89a8c)}
.g6{background:linear-gradient(160deg,#f0e8e1,#c8b1a2)}
/* package */
.package{height:400px;background:linear-gradient(90deg,var(--pink-dark),var(--pink-light));color:var(--white);position:relative;display:flex;justify-content:center;gap:200px;padding-top:40px}
.package-col{position:relative}
.package h3{font-size:18px;font-weight:700;letter-spacing:2px;text-align:center;margin-bottom:18px}
.package-list{list-style:none;width:330px}
.package-list li{display:flex;align-items:center;gap:10px;font-size:12px;margin-bottom:7px}
.package-split{position:absolute;left:0;top:0}
.split-badge{position:absolute;left:560px;top:150px;width:80px;height:80px;border-radius:50%;background:var(--white);border:3px solid var(--pink)}
.quote-form{width:330px}
.field{height:32px;background:var(--white);border-radius:3px;color:#999;font-size:11px;padding:0 12px;display:flex;align-items:center;justify-content:space-between;margin-bottom:10px}
.field.area{height:60px;align-items:flex-start;padding-top:8px}
.form-btn{height:34px;background:var(--blue);border-radius:3px;text-align:center;line-height:34px;font-size:12px;font-weight:700;letter-spacing:1px}
/* contact */
.contact{height:500px;padding-top:40px}
.contact-row{display:flex;justify-content:center;gap:60px;margin-top:40px}
.map{width:470px;height:300px;background:linear-gradient(135deg,#e8e4d8,#cfd8c4 50%,#c6d6e2)}
.contact-info{width:420px}
.contact-info h4{color:var(--pink);font-size:15px;font-weight:700;margin-bottom:14px}
.contact-info .phone{color:var(--pink);font-size:24px;font-weight:700;line-height:1.4}
.contact-info p{font-size:12px;color:#666}
.contact-line{display:flex;align-items:center;gap:10px;margin-top:16px;font-size:12px;color:#666}
/* friends */
.friends{height:320px;background:linear-gradient(180deg,var(--orange-light),var(--orange));padding-top:36px;color:var(--white)}
.friends .section-title{color:var(--white)}
.friend-row{display:flex;justify-content:center;gap:110px;margin-top:26px}
.friend{width:240px;text-align:center}
.friend-badge{width:120px;height:120px;border-radius:50%;background:var(--white);margin:0 auto 14px}
.friend p{font-size:11px}
/* footer */
.site-footer{height:72px;background:var(--dark);color:#aaa;font-size:11px;display:flex;align-items:center;justify-content:space-between;padding:0 90px}
.social{display:flex;gap:8px}
.social span{width:26px;height:26px;border-radius:50%;background:#555}
</style>
</head>
<body>

<header class="site-header">
  <span class="brand-mark"></span>
  <span class="brand-name">T.O.R.U Entertainment</span>
</header>

<nav class="main-nav">
  <a class="active">HOME</a><a>WHAT WE DO</a><a>ABOUT US</a><a>WHY HIRE T.O.R.U?</a><a>COUPLES</a><a>GALLERY</a><a>QUOTE</a><a>CONTACT</a><a>OUR FRIENDS</a>
</nav>

<section class="hero">
  <div class="hero-photo" role="img" aria-label="Photo of a bride and groom embracing, the bride holding a pink rose bouquet"></div>
  <div class="hero-copy">
    <h1>TORU</h1>
    <div class="tagline">Getting rid the earth of boring weddings</div>
    <p>We are a fun and professional wedding team. Our MC and DJ duo keeps every reception lively, warm and personal, so your guests talk about the night for years to come.</p>
    <span class="btn">READ MORE INFO</span>
  </div>
</section>

<section class="services">
  <h2 class="section-title">What we do</h2>
  <svg class="divider" width="60" height="10"><line x1="0" y1="5" x2="22" y2="5" stroke="#e0468a"/><circle cx="30" cy="5" r="3" fill="none" stroke="#e0468a"/><line x1="38" y1="5" x2="60" y2="5" stroke="#e0468a"/></svg>
  <div class="service-cards">
    <div class="service-card pink"><div class="service-icon" role="img" aria-label="Clip-art illustration of a bride and groom"></div><h3>WEDDING MASTER OF CEREMONIES</h3><p>A lively host who runs your timeline, introduces every speech and keeps the room smiling all night.</p><span class="more">READ MORE</span></div>
    <div class="service-card teal"><div class="service-icon" role="img" aria-label="Clip-art illustration of a DJ at turntables"></div><h3>WEDDING DJ</h3><p>Music chosen for your crowd, mixed live on quality gear, so the dance floor stays full until late.</p><span class="more">READ MORE</span></div>
    <div class="service-card orange"><div class="service-icon" role="img" aria-label="Clip-art illustration of champagne glasses"></div><h3>EXTENSIVE PARTY PRE-PLANNING</h3><p>We meet you early, plan each moment with you and handle the details so you can relax.</p><span class="more">READ MORE</span></div>
  </div>
</section>

<section class="about">
  <h2 class="section-title">About us</h2>
  <svg class="divider" width="60" height="10"><line x1="0" y1="5" x2="22" y2="5" stroke="#e0468a"/><circle cx="30" cy="5" r="3" fill="none" stroke="#e0468a"/><line x1="38" y1="5" x2="60" y2="5" stroke="#e0468a"/></svg>
  <div class="about-row">
    <div class="member">
      <div class="member-photo" role="img" aria-label="Portrait photo of the MC"></div>
      <div class="member-name">Ms Delphine</div>
      <p>Delphine is a professional wedding MC with a warm voice and a quick wit. She loves meeting couples and shaping each speech.</p>
    </div>
    <div class="countdown">
      <div class="day">THURSDAY</div>
      <div class="date">31 OCTOBER 2016</div>
      <div class="count-boxes">
        <div class="count-box"><b>24</b><span>DAYS</span></div>
        <div class="count-box"><b>15</b><span>HOURS</span></div>
        <div class="count-box"><b>20</b><span>MINS</span></div>
        <div class="count-box"><b>40</b><span>SECS</span></div>
      </div>
    </div>
    <div class="member">
      <div class="member-photo him" role="img" aria-label="Portrait photo of the DJ"></div>
      <div class="member-name">Mr Anselm</div>
      <p>Anselm has spun music at hundreds of receptions. He reads the room, takes requests and keeps every generation on the dance floor.</p>
    </div>
  </div>
</section>

<section class="why">
  <h2 class="section-title">Why hire T.O.R.U?</h2>
  <svg class="divider" width="60" height="10"><line x1="0" y1="5" x2="22" y2="5" stroke="#fff"/><circle cx="30" cy="5" r="3" fill="none" stroke="#fff"/><line x1="38" y1="5" x2="60" y2="5" stroke="#fff"/></svg>
  <div class="reasons">
    <div class="reason"><span class="reason-icon"><svg width="20" height="20"><path d="M10 17 L3 10 A4 4 0 0 1 10 5 A4 4 0 0 1 17 10 Z" fill="#fff"/></svg></span><div><h4>WE ARE FUN</h4><p>Every detail of your day is planned with care, so the night runs smoothly.</p></div></div>
    <div class="reason"><span class="reason-icon"><svg width="20" height="20"><rect x="3" y="4" width="14" height="13" fill="none" stroke="#fff" stroke-width="2"/><line x1="3" y1="8" x2="17" y2="8" stroke="#fff" stroke-width="2"/></svg></span><div><h4>EXTENSIVE PRE-PLANNING</h4><p>Every detail of your day is planned with care, so the night runs smoothly.</p></div></div>
    <div class="reason"><span class="reason-icon"><svg width="20" height="20"><path d="M4 10 L8 14 L16 5" fill="none" stroke="#fff" stroke-width="2"/></svg></span><div><h4>COMMITTED TO YOU</h4><p>Every detail of your day is planned with care, so the night runs smoothly.</p></div></div>
    <div class="reason"><span class="reason-icon"><svg width="20" height="20"><circle cx="10" cy="10" r="6" fill="none" stroke="#fff" stroke-width="2"/></svg></span><div><h4>PASSION</h4><p>Every detail of your day is planned with care, so the night runs smoothly.</p></div></div>
    <div class="reason"><span class="reason-icon"><svg width="20" height="20"><path d="M10 17 L3 10 A4 4 0 0 1 10 5 A4 4 0 0 1 17 10 Z" fill="none" stroke="#fff" stroke-width="2"/></svg></span><div><h4>EMOTIONAL CONNECTION</h4><p>Every detail of your day is planned with care, so the night runs smoothly.</p></div></div>
    <div class="reason"><span class="reason-icon"><svg width="20" height="20"><polygon points="10,2 12.5,8 19,8 14,12 16,18 10,14 4,18 6,12 1,8 7.5,8" fill="#fff"/></svg></span><div><h4>CREATIVITY</h4><p>Every detail of your day is planned with care, so the night runs smoothly.</p></div></div>
    <div class="reason"><span class="reason-icon"><svg width="20" height="20"><circle cx="7" cy="10" r="4" fill="none" stroke="#fff" stroke-width="2"/><circle cx="13" cy="10" r="4" fill="none" stroke="#fff" stroke-width="2"/></svg></span><div><h4>BOTH IN ONE TEAM</h4><p>Every detail of your day is planned with care, so the night runs smoothly.</p></div></div>
    <div class="reason"><span class="reason-icon"><svg width="20" height="20"><rect x="4" y="7" width="12" height="9" fill="none" stroke="#fff" stroke-width="2"/><rect x="7" y="4" width="6" height="3" fill="none" stroke="#fff" stroke-width="2"/></svg></span><div><h4>PROFESSIONAL ATTITUDE</h4><p>Every detail of your day is planned with care, so the night runs smoothly.</p></div></div>
    <div class="reason"><span class="reason-icon"><svg width="20" height="20"><path d="M8 15 V4 L16 2 V13" fill="none" stroke="#fff" stroke-width="2"/><circle cx="6" cy="15" r="2.5" fill="#fff"/><circle cx="14" cy="13" r="2.5" fill="#fff"/></svg></span><div><h4>MODERN SOUND EQUIPMENT</h4><p>Every detail of your day is planned with care, so the night runs smoothly.</p></div></div>
  </div>
</section>

<section class="couples">
  <div class="couples-photo" role="img" aria-label="Darkened photo of a couple embracing outdoors"></div>
  <div class="couples-inner">
    <h2 class="section-title">Our happy couples</h2>
    <svg class="divider" width="60" height="10"><line x1="0" y1="5" x2="22" y2="5" stroke="#fff"/><circle cx="30" cy="5" r="3" fill="none" stroke="#fff"/><line x1="38" y1="5" x2="60" y2="5" stroke="#fff"/></svg>
    <blockquote>“From the first dance to the last song, the night was pure joy. Our guests laughed, danced and sang, and they still tell us it was the best wedding they have ever been to. Thank you for everything!”</blockquote>
    <div class="couple-avatar" role="img" aria-label="Small photo of the couple"></div>
    <div class="couple-sign">LOVE, NINA &amp; TOMAS</div>
  </div>
</section>

<section class="gallery">
  <h2 class="section-title">Photo gallery</h2>
  <svg class="divider" width="60" height="10"><line x1="0" y1="5" x2="22" y2="5" stroke="#e0468a"/><circle cx="30" cy="5" r="3" fill="none" stroke="#e0468a"/><line x1="38" y1="5" x2="60" y2="5" stroke="#e0468a"/></svg>
  <div class="gallery-grid">
    <div class="gallery-intro"><h3>TORU</h3><p>Fun moments from weddings we have hosted across Sydney this year.</p></div>
    <div class="g1" role="img" aria-label="Photo of a bride and groom kissing"></div>
    <div class="g2" role="img" aria-label="Photo of a bride in a white gown"></div>
    <div class="g3" role="img" aria-label="Photo of an outdoor wedding ceremony"></div>
    <div class="g4" role="img" aria-label="Photo of a smiling couple"></div>
    <div class="g5" role="img" aria-label="Photo of guests at a reception"></div>
    <div class="g6" role="img" aria-label="Photo of a bride and bridesmaids"></div>
  </div>
</section>

<section class="package">
  <svg class="package-split" width="1200" height="400"><line x1="640" y1="40" x2="560" y2="360" stroke="#fff" stroke-width="2"/></svg>
  <span class="split-badge"></span>
  <div class="package-col">
    <h3>OUR WEDDING PACKAGE</h3>
    <ul class="package-list">
      <li><svg width="12" height="12"><path d="M1 6 L5 10 L11 2" fill="none" stroke="#fff" stroke-width="2"/></svg>Wedding MC for the whole reception</li>
      <li><svg width="12" height="12"><path d="M1 6 L5 10 L11 2" fill="none" stroke="#fff" stroke-width="2"/></svg>Professional DJ set all evening</li>
      <li><svg width="12" height="12"><path d="M1 6 L5 10 L11 2" fill="none" stroke="#fff" stroke-width="2"/></svg>State of the art sound system</li>
      <li><svg width="12" height="12"><path d="M1 6 L5 10 L11 2" fill="none" stroke="#fff" stroke-width="2"/></svg>Microphones for speeches and toasts</li>
      <li><svg width="12" height="12"><path d="M1 6 L5 10 L11 2" fill="none" stroke="#fff" stroke-width="2"/></svg>Dance floor lighting</li>
      <li><svg width="12" height="12"><path d="M1 6 L5 10 L11 2" fill="none" stroke="#fff" stroke-width="2"/></svg>Extensive pre-planning meetings</li>
      <li><svg width="12" height="12"><path d="M1 6 L5 10 L11 2" fill="none" stroke="#fff" stroke-width="2"/></svg>Personal music list</li>
      <li><svg width="12" height="12"><path d="M1 6 L5 10 L11 2" fill="none" stroke="#fff" stroke-width="2"/></svg>Set up and pack down</li>
      <li><svg width="12" height="12"><path d="M1 6 L5 10 L11 2" fill="none" stroke="#fff" stroke-width="2"/></svg>Equipment delivery and insurance</li>
    </ul>
  </div>
  <div class="quote-form package-col">
    <h3>REQUEST FORM</h3>
    <div class="field">NUMBER OF GUESTS <svg width="10" height="6"><path d="M0 0 L5 6 L10 0Z" fill="#999"/></svg></div>
    <div class="field">EVENT DURATION <svg width="10" height="6"><path d="M0 0 L5 6 L10 0Z" fill="#999"/></svg></div>
    <div class="field">VENUE SUBURB <svg width="10" height="6"><path d="M0 0 L5 6 L10 0Z" fill="#999"/></svg></div>
    <div class="field area">COMMENTS</div>
    <div class="form-btn">GET INSTANT QUOTE</div>
  </div>
</section>

<section class="contact">
  <h2 class="section-title">Contact us</h2>
  <svg class="divider" width="60" height="10"><line x1="0" y1="5" x2="22" y2="5" stroke="#e0468a"/><circle cx="30" cy="5" r="3" fill="none" stroke="#e0468a"/><line x1="38" y1="5" x2="60" y2="5" stroke="#e0468a"/></svg>
  <div class="contact-row">
    <div class="map" role="img" aria-label="Street map showing the company location"></div>
    <div class="contact-info">
      <h4>We'd love to hear from you!</h4>
      <div class="phone">0400 123 987</div>
      <p>Contact us on 0400 123 987 or send a note through the form. We reply within one day and are happy to chat about your plans.</p>
      <div class="contact-line"><svg width="16" height="12"><rect x="0.5" y="0.5" width="15" height="11" fill="none" stroke="#e0468a"/><path d="M0.5 0.5 L8 7 L15.5 0.5" fill="none" stroke="#e0468a"/></svg>hello@toru-entertainment.com</div>
      <div class="contact-line"><svg width="16" height="16"><circle cx="8" cy="8" r="7" fill="none" stroke="#e0468a"/><line x1="1" y1="8" x2="15" y2="8" stroke="#e0468a"/></svg>www.toru-entertainment.com</div>
      <div class="contact-line"><svg width="14" height="16"><path d="M7 15 C2 9 1 7 1 6 A6 6 0 0 1 13 6 C13 7 12 9 7 15Z" fill="#e0468a"/></svg>Sydney, NSW</div>
    </div>
  </div>
</section>

<section class="friends">
  <h2 class="section-title">Our trusted friends</h2>
  <svg class="divider" width="60" height="10"><line x1="0" y1="5" x2="22" y2="5" stroke="#fff"/><circle cx="30" cy="5" r="3" fill="none" stroke="#fff"/><line x1="38" y1="5" x2="60" y2="5" stroke="#fff"/></svg>
  <div class="friend-row">
    <div class="friend"><div class="friend-badge"></div><p>A trusted partner we work with often, known for friendly service and beautiful results.</p></div>
    <div class="friend"><div class="friend-badge"></div><p>A trusted partner we work with often, known for friendly service and beautiful results.</p></div>
    <div class="friend"><div class="friend-badge"></div><p>A trusted partner we work with often, known for friendly service and beautiful results.</p></div>
  </div>
</section>

<footer class="site-footer">
  <span>© Copyright 2016, T.O.R.U All Rights Reserved.</span>
  <div class="social"><span></span><span></span><span></span><span></span><span></span><span></span></div>
</footer>

</body>
</html>
```